Brookvane Consulting Business Card Design

Business Card Design for Brookvane Consulting. Brookvane Consulting is a boutique consultancy based in Atlanta, GA., that specializes in marketing strategy, organization planning, and leadership development. We provide solutions for small businesses and startups as well as Vantage 300 companies.

http://brookvaneconsulting.com/

Target Market(s)

We provide solutions for small businesses and startups as well as Vantage 300 companies.

Industry/Entity Type

Consulting

Contact Information for Business Card

Two sided business card with priority on contact information, logo, tag line (Inspiration to Dream More, Do More, Become More)

Colors

Designer to choose colors to be used in the design.

Requirements
Must have
• contact information, logo, tag line (Inspiration to Dream More, Do More, Become More)
• Simple no over communication.
Nice to have
• I would like to see different placements of logo and creative use of both sides of the card
Should not have
• Do not put too much information on the card.

```html
<!DOCTYPE html>
<html lang="en">
<head>
<meta charset="utf-8">
<title>Brookvane Consulting – Business Card</title>
<link href="https://fonts.googleapis.com/css2?family=Lato:wght@300;400;700&display=swap" rel="stylesheet">
<style>
  :root {
    --backdrop: #4a423c;
    --card-dark: #39393a;
    --card-light: #ffffff;
    --ink: #2e2e2e;
    --ink-soft: #555555;
    --on-dark: #ffffff;
    --on-dark-soft: #cfcfcf;
  }
  * { margin: 0; padding: 0; box-sizing: border-box; }
  html, body {
    width: 1200px; height: 930px; overflow: hidden;
    background: var(--backdrop);
    font-family: "Lato", sans-serif;
  }
  .canvas { position: relative; width: 1200px; height: 930px; }
  .card {
    position: absolute; width: 640px; height: 366px; border-radius: 18px; overflow: hidden;
  }
  .card--front { left: 150px; top: 70px; background: var(--card-dark); }
  .card--back { left: 410px; top: 494px; background: var(--card-light); }

  .brand {
    position: absolute; left: 50%; top: 50%; transform: translate(-50%, -50%);
    display: flex; flex-direction: column; align-items: center; gap: 16px;
  }
  .wordmark {
    display: flex; align-items: center; gap: 12px; white-space: nowrap;
    font-family: "Lato", sans-serif; font-weight: 400; letter-spacing: 1px;
  }
  .wordmark__square { width: 18px; height: 18px; flex: none; }
  .card--front .wordmark { color: var(--on-dark); font-size: 40px; }
  .card--front .wordmark__square { background: var(--on-dark); }
  .tagline {
    font-size: 14px; font-weight: 300; letter-spacing: 1.5px; white-space: nowrap;
    color: var(--on-dark-soft);
  }

  .card--back .wordmark {
    position: absolute; right: 40px; top: 212px; color: var(--ink); font-size: 26px;
  }
  .card--back .wordmark__square { background: var(--ink); width: 14px; height: 14px; }

  .contact { position: absolute; left: 40px; top: 56px; color: var(--ink-soft); white-space: nowrap; }
  .contact__name {
    font-weight: 700; font-size: 22px; color: var(--ink); letter-spacing: 0.5px;
  }
  .contact__role { font-size: 15px; font-weight: 400; margin-bottom: 8px; }
  .contact__address { font-size: 15px; line-height: 1.3; margin-bottom: 8px; font-weight: 300; }
  .contact__list { list-style: none; font-size: 15px; font-weight: 300; }
  .contact__item { display: flex; align-items: center; gap: 10px; line-height: 1.35; }
  .contact__icon { width: 12px; height: 12px; flex: none; }
</style>
</head>
<body>
<main class="canvas">
  <section class="card card--front" aria-label="Card front">
    <div class="brand">
      <div class="wordmark"><span class="wordmark__square"></span>Brookvane Consulting</div>
      <p class="tagline">Inspiration to Dream More, Do More, Become More</p>
    </div>
  </section>

  <section class="card card--back" aria-label="Card back">
    <div class="contact">
      <p class="contact__name">DANIEL REYES</p>
      <p class="contact__role">Director</p>
      <p class="contact__address">1420 Peachtree St NE,<br>Atlanta, GA 30309</p>
      <ul class="contact__list">
        <li class="contact__item">
          <svg class="contact__icon" viewBox="0 0 12 12"><path d="M2 1l2 0 1 3-1.5 1a6 6 0 0 0 3.5 3.5L8 7l3 1v2a1 1 0 0 1-1 1A9 9 0 0 1 1 2a1 1 0 0 1 1-1z" fill="#333"/></svg>
          +1 404 555-0142
        </li>
        <li class="contact__item">
          <svg class="contact__icon" viewBox="0 0 12 12"><rect x="3" y="0.5" width="6" height="11" rx="1" fill="none" stroke="#333" stroke-width="1.3"/><circle cx="6" cy="9.5" r="0.8" fill="#333"/></svg>
          +1 404 555-0187
        </li>
        <li class="contact__item">
          <svg class="contact__icon" viewBox="0 0 12 12"><rect x="0.7" y="2.2" width="10.6" height="7.6" fill="none" stroke="#333" stroke-width="1.2"/><path d="M1 2.5l5 4 5-4" fill="none" stroke="#333" stroke-width="1.2"/></svg>
          BrookvaneConsulting.com
        </li>
        <li class="contact__item">
          <svg class="contact__icon" viewBox="0 0 12 12"><circle cx="6" cy="6" r="5.2" fill="none" stroke="#333" stroke-width="1.1"/><ellipse cx="6" cy="6" rx="2.2" ry="5.2" fill="none" stroke="#333" stroke-width="1"/><path d="M1 6h10" stroke="#333" stroke-width="1"/></svg>
          www.BrookvaneConsulting.com
        </li>
      </ul>
    </div>
    <div class="wordmark"><span class="wordmark__square"></span>Brookvane Consulting</div>
  </section>
</main>
</body>
</html>
```